professional business card design

Business card design. Photos have been uploaded and i am open to the designer choosing which photos to use. Would like the card to be mostyly in a grey scale design with black, whites, silver & grey colours. I have added copy of our flyer as would like on the back side of card our services to be listed. Do not use any bright colurs such as blue red green or yellow. i need to be able to edit the phone number and naem in the final card design submitted.

Target Market(s)

Clients

Industry/Entity Type

earhmovibng and transport

Contact Information for Business Card

Director Name, address, email, phone number and services

Colors

Designer to choose only greyscale colors for use in the design.

Requirements
Should not have
• no yellow, red, blue or green

```html
<!DOCTYPE html>
<html lang="en">
<head>
<meta charset="utf-8">
<title>Ridgeline Business Card</title>
<link rel="stylesheet" href="https://fonts.googleapis.com/css2?family=Arimo:ital,wght@0,400;0,700;1,400&display=swap">
<style>
  :root {
    --page: #2b2b2d;
    --card-dark: #0c0c0d;
    --card-mid: #1d1d1f;
    --text: #ffffff;
    --text-soft: #d6d6d6;
    --text-muted: #a9a9ab;
    --silver: #c9c9cc;
    --photo-sky: #a9c4d8;
    --photo-ground: #8e7f6d;
    --photo-truck: #e3e6ea;
  }
  * { box-sizing: border-box; margin: 0; padding: 0; }
  html, body {
    width: 1200px; height: 1015px; overflow: hidden;
    background: var(--page);
    font-family: "Arimo", Arial, sans-serif;
    color: var(--text);
  }
  .canvas { position: relative; width: 1200px; height: 1015px; }
  .card {
    position: absolute; left: 190px; width: 820px; height: 470px;
    overflow: hidden;
    background: radial-gradient(ellipse at 60% 40%, var(--card-mid) 0%, var(--card-dark) 75%);
    box-shadow: 0 18px 40px rgba(0,0,0,.55);
  }
  .card--services { top: 30px; }
  .card--contact { top: 515px; }

  /* services side */
  .photo-circle {
    position: absolute; left: 360px; top: -150px;
    width: 560px; height: 560px; border-radius: 50%;
    background: linear-gradient(180deg, var(--photo-sky) 0%, #c8d6e0 45%, var(--photo-truck) 60%, var(--photo-ground) 100%);
  }
  .services {
    position: absolute; left: 40px; top: 78px; width: 470px;
  }
  .services__title {
    font-weight: 700; font-size: 22px; letter-spacing: .5px; margin-bottom: 6px;
  }
  .services__list { list-style: none; }
  .services__list li {
    font-size: 18px; line-height: 22.5px; position: relative; padding-left: 20px;
  }
  .services__list li::before {
    content: ""; position: absolute; left: 2px; top: 7px;
    width: 9px; height: 9px; border-radius: 50%; background: var(--text);
  }
  .services__note {
    margin-top: 12px; font-size: 18px; line-height: 22px; font-style: italic; padding-left: 20px;
  }
  .services__note strong { font-style: normal; font-weight: 700; }

  /* contact side */
  .person { position: absolute; left: 60px; top: 150px; }
  .person__name { font-size: 28px; font-weight: 700; letter-spacing: 1px; color: var(--text-soft); }
  .person__role { font-size: 17px; letter-spacing: 1px; color: var(--text-muted); margin-top: 2px; }
  .contact-list { list-style: none; margin-top: 36px; }
  .contact-list li {
    display: flex; align-items: center; gap: 10px;
    font-size: 19px; line-height: 27px; color: var(--text-soft);
  }
  .contact-list svg { width: 18px; height: 18px; flex: none; }
  .address { margin-top: 34px; font-size: 19px; line-height: 25px; color: var(--text-soft); }
  .brand {
    position: absolute; right: 60px; top: 120px;
    display: flex; align-items: center; gap: 16px;
    font-size: 56px; font-weight: 700; letter-spacing: 2px; color: var(--silver);
  }
  .brand__dot { width: 26px; height: 26px; border-radius: 50%; background: var(--silver); }
</style>
</head>
<body>
<main class="canvas">

  <section class="card card--services">
    <div class="photo-circle" role="img" aria-label="Photo of a white prime mover hauling heavy earthmoving machinery on a low loader under a cloudy sky"></div>
    <div class="services">
      <h2 class="services__title">OUR SERVICES</h2>
      <ul class="services__list">
        <li>Over size loads/hot shot loads</li>
        <li>Heavy vehicle recovery services</li>
        <li>Potable water deliveries</li>
        <li>Road building/mainttenance</li>
        <li>Earthworks</li>
        <li>Sand &amp; metal supply &amp; cartage</li>
        <li>Road train tippers</li>
        <li>Road train tankers</li>
        <li>Road train flat tops</li>
        <li>Drop deck trailers</li>
        <li>Mine site accredited</li>
        <li>Equipment &amp; operators</li>
      </ul>
      <p class="services__note">we offer a large range of services not listed <strong>so call us today for a personalised quote to suit your needs.</strong></p>
    </div>
  </section>

  <section class="card card--contact">
    <div class="brand"><span class="brand__dot"></span>RIDGELINE</div>
    <div class="person">
      <h1 class="person__name">MARCUS HALE</h1>
      <p class="person__role">MANAGING DIRECTOR</p>
      <ul class="contact-list">
        <li>
          <svg viewBox="0 0 24 24" fill="#d6d6d6" aria-hidden="true"><path d="M6.6 10.8a15.1 15.1 0 0 0 6.6 6.6l2.2-2.2c.3-.3.7-.4 1-.2 1.1.4 2.3.6 3.6.6.6 0 1 .4 1 1V20c0 .6-.4 1-1 1A17 17 0 0 1 3 4c0-.6.4-1 1-1h3.5c.6 0 1 .4 1 1 0 1.3.2 2.5.6 3.6.1.3 0 .7-.2 1z"/></svg>
          055-318 274 960
        </li>
        <li>
          <svg viewBox="0 0 24 24" fill="none" stroke="#d6d6d6" stroke-width="2" aria-hidden="true"><rect x="3" y="5" width="18" height="14"/><path d="M3 5l9 8 9-8"/></svg>
          hello@ridgelinehaul.com
        </li>
        <li>
          <svg viewBox="0 0 24 24" fill="none" stroke="#d6d6d6" stroke-width="2" aria-hidden="true"><circle cx="12" cy="12" r="9"/><path d="M3 12h18M12 3c3 3 3 15 0 18M12 3c-3 3-3 15 0 18"/></svg>
          www.ridgelinehaul.com
        </li>
      </ul>
      <p class="address">87, Quarry Road Depot<br>61208, Northfield</p>
    </div>
  </section>

</main>
</body>
</html>
```